Brand and Marketing Coach Needs PDF Designed

I have content that i need placed into a simple but great PDF design. The PDF is about the formula I use to build personal brands. This is geared towards entrepreneurs, experts, coaches, therapists, wellness practitioners, and indpendent business owners who serve to improve the lives of others.
The company name is changing from TorvelCast to Selling with the Village (I don't have that logo yet, so working backwards a bit. For now, the TorvelCast logo can be used.) My brand is NOT formal and corporate, but it's also not neon-pink and screaming at you. It's down to earth, hip, a bit modern but warm. It's about no BS and authenticity. The final deliverable should make the reader feel focused, smart, motivated and hopeful.

Target Market(s)

Conscious entrepreneurs and small business owners. this one is specifically for pharmacy entrepreneurs but this will be used for various audiences later.

Font styles to use
Sans Serif

Colors
eaf1f7
3377b5
6b449b
f37122
faa54b
f68e4e
ffc214

Requirements
Must have
• Modern design. colors that match logo - 4e5583 (i think that is the blue.) d65a40.
• Could have these colors as well: c6a254, 01bcc3
• But open to other colors
Nice to have
• I'd like to see some ways to make this PDF simple and readable, and eye-catching. I'd also like to use the uploaded ebooks for design ideas.
Should not have
• neon colors, clip art

```html
<!DOCTYPE html>
<html lang="en">
<head>
<meta charset="utf-8">
<title>Follow the Personal Brand Formula – Workbook Spreads</title>
<link href="https://fonts.googleapis.com/css2?family=Playfair+Display:wght@400&family=Cormorant+Garamond:ital,wght@0,400;0,600;0,700;1,400&display=swap" rel="stylesheet">
<style>
  :root {
    --page-indigo: #4f5683;
    --paper: #ffffff;
    --ink-light: #ffffff;
    --field: #ffffff;
  }
  html, body {
    margin: 0;
    padding: 0;
    width: 1200px;
    height: 957px;
    overflow: hidden;
    background: var(--paper);
  }
  .canvas {
    position: relative;
    width: 1200px;
    height: 957px;
  }
  .page {
    position: absolute;
    width: 544px;
    height: 427px;
    background: var(--page-indigo);
    color: var(--ink-light);
    font-family: "Cormorant Garamond", Georgia, serif;
  }
  .page--intro   { left: 45px;  top: 38px; }
  .page--chapter { left: 611px; top: 38px; }
  .page--step    { left: 45px;  top: 492px; }
  .page--worksheet { left: 611px; top: 492px; }

  .page-number {
    position: absolute;
    left: 0; right: 0;
    top: 390px;
    text-align: center;
    font-size: 6.5px;
    letter-spacing: 0.3px;
    text-transform: uppercase;
  }

  .intro-copy {
    position: absolute;
    left: 50px;
    top: 59px;
    width: 436px;
    font-size: 9.6px;
    line-height: 11.6px;
  }
  .intro-copy p { margin: 0 0 11.6px; }

  .chapter-number {
    position: absolute;
    left: 0; right: 0;
    top: 58px;
    text-align: center;
    font-family: "Playfair Display", Georgia, serif;
    font-size: 132px;
    line-height: 1;
  }
  .chapter-title {
    position: absolute;
    left: 0; right: 0;
    top: 187px;
    margin: 0;
    text-align: center;
    font-family: "Playfair Display", Georgia, serif;
    font-weight: 400;
    font-size: 47px;
    line-height: 62px;
    letter-spacing: 0.5px;
  }

  .step-heading {
    position: absolute;
    left: 50px;
    top: 46px;
    display: flex;
    align-items: center;
    gap: 13px;
    margin: 0;
    font-family: "Playfair Display", Georgia, serif;
    font-weight: 400;
    font-size: 20px;
    letter-spacing: 0.3px;
  }
  .step-badge {
    width: 32px;
    height: 32px;
    border-radius: 50%;
    background: var(--ink-light);
    color: var(--page-indigo);
    display: flex;
    align-items: center;
    justify-content: center;
    font-family: "Cormorant Garamond", Georgia, serif;
    font-style: italic;
    font-size: 22px;
  }
  .step-body {
    position: absolute;
    left: 50px;
    top: 93px;
    width: 443px;
  }
  .step-subtitle {
    margin: 0;
    font-size: 13.5px;
    font-weight: 600;
    line-height: 14px;
  }
  .step-body p {
    margin: 0 0 10px;
    font-size: 9.8px;
    line-height: 11.5px;
  }

  .prompt {
    position: absolute;
    left: 50px;
    width: 443px;
    margin: 0;
    font-style: italic;
    font-size: 9.4px;
    line-height: 11.6px;
  }
  .answer-field {
    position: absolute;
    left: 50px;
    width: 443px;
    background: var(--field);
  }

  .worksheet-label {
    position: absolute;
    left: 50px;
    top: 156px;
    margin: 0;
    font-size: 12.5px;
    font-weight: 700;
  }
  .motivator-grid {
    position: absolute;
    left: 50px;
    top: 204px;
    width: 443px;
    display: grid;
    grid-template-columns: 217px 217px;
    column-gap: 9px;
    row-gap: 7px;
  }
  .motivator-grid span {
    display: block;
    height: 24px;
    background: var(--field);
  }
</style>
</head>
<body>
<main class="canvas">

  <section class="page page--intro">
    <div class="intro-copy">
      <p>Your personal brand will define how you present yourself on all your marketing platforms – on and off-line. It’s everything you and your team say and do. It’s what you blog about, how you write, the photos you share. It’s the message that comes through loud and clear every time, even when no words are uttered.</p>
      <p>Without a brand, you fade into online oblivion.</p>
      <p>This is your foundation and the BLUEPRINT for all you do.</p>
    </div>
    <div class="page-number">Page x of xx</div>
  </section>

  <section class="page page--chapter">
    <div class="chapter-number">3</div>
    <h1 class="chapter-title">FOLLOW THE<br>PERSONAL<br>BRAND FORMULA</h1>
  </section>

  <section class="page page--step">
    <h2 class="step-heading"><span class="step-badge">1</span>MOTIVATORS</h2>
    <div class="step-body">
      <h3 class="step-subtitle">Your WHY and the real reason you created this business.</h3>
      <p>This is what motivates you to serve people as you do, and the purpose behind your business. Because your personal brand must reflect your purpose and values, your mission, tagline, and messaging won’t align with you or communicate your real value. When this happens, you attract the wrong clients or none at all. When your purpose is driving your business, it flows much easier, and you are happy doing LIFE!</p>
      <p>Similar to core values and core values can come from this for sure, but our focus is not so much on your messaging right now, as it is on your how you’re positioning yourself. Messaging comes later. Right now, we’re honing in on what makes you unique.</p>
    </div>
    <p class="prompt" style="top:218px;">What is your WHY- the real reason the creation of this business/company? This is also your story -It is something that got you to where you are today, doing what you are doing to serve your clients.</p>
    <div class="answer-field" style="top:247px; height:52px;"></div>
    <p class="prompt" style="top:311px;">What do you passionately stand for?</p>
    <div class="answer-field" style="top:328px; height:35px;"></div>
    <div class="page-number">Page x of xx</div>
  </section>

  <section class="page page--worksheet">
    <p class="prompt" style="top:40px;">What do you believe - what’s your philosophy - and how is that different. (Maybe you hate B.S. but are in an industry that if full of it, maybe you see how people have been teaching us something wrong about nutrition and you have an entirely new perspective and form of healing you offer your clients.)</p>
    <div class="answer-field" style="top:85px; height:52px;"></div>
    <h3 class="worksheet-label">Your Motivators:</h3>
    <p class="prompt" style="top:172px;">From the answers above, choose 3 - 6 phrases or sentences that stand out most to you and write them blow in a way that unifies them.</p>
    <div class="motivator-grid">
      <span></span><span></span>
      <span></span><span></span>
      <span></span><span></span>
    </div>
    <div class="page-number">Page x of xx</div>
  </section>

</main>
</body>
</html>
```